Creative, fresh business card design for Ripplecraft Facades

We need a fresh, creative business card design for Ripplecraft Facades. We are the manufacturer of Ripplecraft Facades in Australia. Wall panels are 2400 x 1200mm panels made from MDF and feature 3D patterns on the face of the panel. The colours to be used are green, silver/grey and white RGB
Red 187
Green 207
Blue 65.

An idea is to possibly use a watermark of one of our designs as a background (like on the "Grids" design on the left hand side of page 2 of our brochure).

Target Market(s)

Interior designers, architects, builders and home renovators

Industry/Entity Type

Business

Contact Information for Business Card

Details to go on the card are:
Our logo (attached),
Slogan: "Decorative panels for interiors and exteriors",
Contact name,
Position,
Mobile phone number,
Business address,
Business phone,
Business fax,
Website and
Email address.

I have attached a few images of our panels and our brochure for reference.

The colours of the business card should feature our logo colours which are: RGB
Red 187
Green 207
Blue 65

Requirements
Must have
• Very modern fonts and design. Some of the designs shown especially the "Prisms" design which is a popular design.
Nice to have
• Creative but simple design. Very contemporary.
Should not have
• Anything ornate or old fashioned.

```html
<!DOCTYPE html>
<html lang="en">
<head>
<meta charset="utf-8">
<title>Ripplecraft Facades – Business Card</title>
<link href="https://fonts.googleapis.com/css2?family=Open+Sans:wght@400;600;700&display=swap" rel="stylesheet">
<style>
  :root {
    --backdrop: #5f5f5f;
    --card: #f4f4f4;
    --lime: #bbcf41;
    --silver: #939497;
    --ink: #2a2a2a;
    --white: #ffffff;
  }
  * { margin: 0; padding: 0; box-sizing: border-box; }
  html, body { width: 1200px; height: 900px; overflow: hidden; }
  body {
    background: var(--backdrop);
    font-family: "Open Sans", Arial, sans-serif;
    position: relative;
  }
  .card {
    position: absolute;
    top: 306px;
    width: 439px;
    height: 271px;
    border-radius: 10px;
    overflow: hidden;
    background: var(--card);
  }
  .card--front { left: 149px; }
  .card--back { left: 609px; }

  /* Front */
  .brand {
    position: absolute;
    left: 192px; top: 395px;
  }
  .front-brand { position: absolute; left: 40px; top: 60px; width: 175px; text-align: center; }
  .brand-mark {
    display: inline-block;
    width: 34px; height: 34px;
    background: var(--lime);
    margin-bottom: 10px;
  }
  .brand-name {
    display: block;
    font-size: 17px;
    font-weight: 600;
    color: var(--silver);
    line-height: 1.2;
  }
  .tagline {
    margin-top: 10px;
    font-size: 10px;
    letter-spacing: 1.6px;
    color: #a4a5a7;
    line-height: 1.25;
  }
  .contact {
    position: absolute;
    left: 249px; top: 44px;
    color: var(--ink);
    font-size: 12px;
  }
  .contact-name {
    color: var(--lime);
    font-weight: 700;
    font-size: 14px;
    letter-spacing: 0.3px;
    line-height: 1.2;
  }
  .contact-role { font-size: 12px; margin-top: 1px; }
  .contact-lines { list-style: none; margin-top: 14px; }
  .contact-lines li {
    display: flex; align-items: center;
    height: 16px; line-height: 16px;
  }
  .contact-lines svg { width: 9px; height: 9px; margin-right: 7px; fill: var(--lime); }
  .address { margin-top: 11px; line-height: 16px; padding-left: 1px; }

  .footer-band { position: absolute; left: 0; bottom: 0; width: 439px; height: 42px; }
  .website {
    position: absolute;
    left: 0; bottom: 16px; width: 240px;
    text-align: center;
    color: var(--white);
    font-size: 11px; font-weight: 700;
  }

  /* Back */
  .ripple-texture {
    position: absolute; inset: 0;
    background: linear-gradient(160deg, #f2f2f2 0%, #dcdcdc 35%, #efefef 60%, #d6d6d6 100%);
  }
  .back-brand {
    position: absolute;
    left: 0; top: 84px; width: 100%;
    text-align: center;
  }
  .back-brand .brand-mark { width: 46px; height: 46px; margin-bottom: 14px; }
  .back-brand .brand-name { font-size: 26px; }
</style>
</head>
<body>

<section class="card card--front">
  <div class="front-brand">
    <span class="brand-mark"></span>
    <span class="brand-name">Ripplecraft Facades</span>
    <p class="tagline">decorative panels for<br>interiors &amp; landscapes</p>
  </div>

  <div class="contact">
    <p class="contact-name">MARCUS ELLERY</p>
    <p class="contact-role">Managing Director</p>
    <ul class="contact-lines">
      <li><svg viewBox="0 0 10 10"><rect x="2.5" y="0" width="5" height="10" rx="1"/></svg>044-555 210 384</li>
      <li><svg viewBox="0 0 10 10"><path d="M0 4 Q5 0 10 4 L8 5 L7 4 L3 4 L2 5 Z M2 6 H8 V10 H2 Z"/></svg>044-555 210 385</li>
      <li><svg viewBox="0 0 10 10"><rect x="1" y="3" width="8" height="7"/><rect x="2.5" y="0" width="5" height="3"/></svg>044-555 210 386</li>
      <li><svg viewBox="0 0 10 10"><path d="M0 2 H10 V9 H0 Z M0 2 L5 6 L10 2"/></svg>hello@ripplecraft.net</li>
    </ul>
    <p class="address">48 Kiln Street, Geelong<br>Australia, 3220.</p>
  </div>

  <svg class="footer-band" viewBox="0 0 439 42" aria-hidden="true">
    <polygon points="0,0 213,0 244,42 0,42" fill="var(--lime)"/>
    <polygon points="233,13 439,13 439,42 252,42" fill="var(--silver)"/>
  </svg>
  <p class="website">www.ripplecraft.net</p>
</section>

<section class="card card--back">
  <div class="ripple-texture" role="img" aria-label="Soft white wave-relief wall panel texture"></div>
  <div class="back-brand">
    <span class="brand-mark"></span>
    <span class="brand-name">Ripplecraft Facades</span>
  </div>
</section>

</body>
</html>
```